Brintel Works - Fast, Efficient and Gas Mainteance for Domestic, Commercial and Industrial clients

We are in the process of purchasing a new business and would like to get a new logo and business card.
Business is a gas maintenance business that also does new gas installations.
Has been established since 1988.
Services include:
Install all types of gas appliances & equipment inc. hot water units
Maintain / repair / replace all types of gas appliances & equipment

Target Market(s)

Domestic, Commercial and Industrial clients

Industry/Entity Type

Business

Contact Information for Business Card

admin@brintelworks.com.au
07 3918 4726
Brintel Works PTY LTD

Logo Text

Gas Fitting & Plumbing Maintenance Specialists

Font styles to use
Sans Serif

Requirements
Must have
• Logo
• Business name, contact number, email address, web address
• Domestic | Commercial | Industrial Est Since 1988
Nice to have
• Possibly a black card with a flame logo to one side
Should not have
• Spelling errors

```html
<!DOCTYPE html>
<html lang="en">
<head>
<meta charset="utf-8">
<title>Brintel Works – Business Card</title>
<link rel="stylesheet" href="https://fonts.googleapis.com/css2?family=Roboto:wght@400;500;700;900&display=swap">
<style>
  :root {
    --bg: #ececea;
    --card-black: #050505;
    --brand-orange: #f7a21b;
    --grad-top: #ffc107;
    --grad-bottom: #ff6a00;
    --ink: #111111;
    --white: #ffffff;
  }
  * { box-sizing: border-box; margin: 0; padding: 0; }
  html, body {
    width: 1200px;
    height: 857px;
    overflow: hidden;
    background: var(--bg);
    font-family: "Roboto", Arial, sans-serif;
  }
  .canvas {
    width: 1200px;
    height: 857px;
    display: flex;
    align-items: center;
    justify-content: center;
    gap: 60px;
  }
  .card {
    width: 510px;
    height: 312px;
    border-radius: 30px;
    position: relative;
    overflow: hidden;
  }
  /* Front */
  .card--front {
    background: var(--card-black);
    display: flex;
    align-items: center;
    justify-content: center;
  }
  .brand-lockup {
    display: flex;
    align-items: center;
    gap: 14px;
  }
  .brand-lockup__name {
    color: var(--brand-orange);
    font-weight: 700;
    font-size: 44px;
    letter-spacing: 2px;
    text-transform: uppercase;
  }
  .brand-lockup__dot {
    width: 30px;
    height: 30px;
    border-radius: 50%;
    background: var(--brand-orange);
  }
  /* Back */
  .card--back {
    background: linear-gradient(180deg, var(--grad-top) 0%, var(--grad-bottom) 100%);
    color: var(--ink);
    display: flex;
    flex-direction: column;
    align-items: center;
  }
  .back-brand {
    margin-top: 58px;
    display: flex;
    flex-direction: column;
    align-items: center;
    gap: 10px;
  }
  .back-brand__mark {
    width: 52px;
    height: 52px;
    border-radius: 50%;
    border: 7px solid var(--ink);
  }
  .back-brand__name {
    font-weight: 700;
    font-size: 17px;
    letter-spacing: 2px;
    text-transform: uppercase;
  }
  .sectors {
    margin-top: 26px;
    font-size: 12.5px;
    letter-spacing: 0.6px;
    text-transform: uppercase;
  }
  .sectors .sep { margin: 0 5px; color: var(--white); }
  .contact-row {
    position: absolute;
    left: 0;
    right: 0;
    bottom: 26px;
    display: flex;
    justify-content: center;
    gap: 14px;
    font-size: 12.5px;
    color: var(--white);
  }
  .contact-item {
    display: flex;
    align-items: center;
    gap: 5px;
  }
  .contact-item--phone { font-weight: 700; color: var(--ink); }
  .contact-icon { width: 12px; height: 12px; flex: none; }
</style>
</head>
<body>
  <main class="canvas">
    <section class="card card--front" aria-label="Card front">
      <div class="brand-lockup">
        <span class="brand-lockup__name">Brintel Works</span>
        <span class="brand-lockup__dot" aria-hidden="true"></span>
      </div>
    </section>

    <section class="card card--back" aria-label="Card back">
      <div class="back-brand">
        <span class="back-brand__mark" aria-hidden="true"></span>
        <span class="back-brand__name">Brintel Works</span>
      </div>
      <p class="sectors">Domestic<span class="sep">•</span>Commercial<span class="sep">•</span>Industrial Est Since 1988</p>
      <div class="contact-row">
        <span class="contact-item">
          <svg class="contact-icon" viewBox="0 0 12 12" aria-hidden="true"><circle cx="6" cy="6" r="6" fill="#fff"/><rect x="3" y="4" width="6" height="4" fill="none" stroke="#ff6a00" stroke-width="1"/><path d="M3 4l3 2.2L9 4" fill="none" stroke="#ff6a00" stroke-width="1"/></svg>
          admin@brintelworks.com.au
        </span>
        <span class="contact-item contact-item--phone">
          <svg class="contact-icon" viewBox="0 0 12 12" aria-hidden="true"><circle cx="6" cy="6" r="6" fill="#fff"/><path d="M4 3.2l1.2 1.4-.6.8a4 4 0 0 0 2 2l.8-.6 1.4 1.2-.7 1A5 5 0 0 1 3 4z" fill="#ff6a00"/></svg>
          07 3918 4726
        </span>
        <span class="contact-item">
          <svg class="contact-icon" viewBox="0 0 12 12" aria-hidden="true"><circle cx="6" cy="6" r="6" fill="#fff"/><circle cx="6" cy="6" r="3.2" fill="none" stroke="#ff6a00" stroke-width="1"/><path d="M2.8 6h6.4M6 2.8v6.4" stroke="#ff6a00" stroke-width="0.8"/></svg>
          brintelworks.com.au
        </span>
      </div>
    </section>
  </main>
</body>
</html>
```